Harborline Auto LLC

Car Dealer Customer Service
Address: 2874 Cresthaven Road, Shelbyville, TN 37162
web: www.harborlineautoxq.net
email: harborlineautoxq@mailnest.example
Phone: (931) 555-0148
Phone: (629) 555-0173

```html
<!DOCTYPE html>
<html lang="en">
<head>
<meta charset="utf-8">
<title>Harborline Auto – Business Card</title>
<link href="https://fonts.googleapis.com/css2?family=Poppins:wght@400;500;600;700&display=swap" rel="stylesheet">
<style>
  :root {
    --backdrop: #262729;
    --card-dark: #2a2b2f;
    --card-dark-edge: #232427;
    --brand-blue: #1f6ea3;
    --brand-blue-light: #2a85bd;
    --name-blue: #2b8fd2;
    --gold: #e2a53a;
    --text-light: #e6e6e8;
    --emboss: #3b3c41;
  }
  html, body {
    margin: 0;
    padding: 0;
    width: 1200px;
    height: 1138px;
    overflow: hidden;
    background: var(--backdrop);
    font-family: "Poppins", sans-serif;
  }
  .card {
    position: absolute;
    width: 620px;
    height: 374px;
    border-radius: 16px;
    overflow: hidden;
    background: linear-gradient(160deg, var(--card-dark) 0%, var(--card-dark-edge) 100%);
  }
  .card--front { left: 274px; top: 186px; }
  .card--back  { left: 276px; top: 608px; }

  /* Front */
  .front-mark {
    position: absolute;
    left: 0; right: 0;
    top: 150px;
    text-align: center;
    font-weight: 700;
    font-size: 34px;
    letter-spacing: 1px;
    color: var(--emboss);
  }
  .front-web {
    position: absolute;
    left: 0; right: 0;
    top: 333px;
    display: flex;
    justify-content: center;
    align-items: center;
    gap: 20px;
    font-size: 15px;
    color: var(--text-light);
  }
  .front-web .rule {
    width: 54px;
    height: 2px;
    background: var(--gold);
  }

  /* Back */
  .back-band {
    position: absolute;
    left: 0; top: 0;
    width: 620px; height: 374px;
  }
  .brand-circle {
    position: absolute;
    left: 95px; top: 108px;
    width: 110px; height: 110px;
    border-radius: 50%;
    background: rgba(255,255,255,0.92);
  }
  .brand-name {
    position: absolute;
    left: 0; width: 300px;
    top: 250px;
    text-align: center;
    font-weight: 700;
    font-size: 22px;
    color: #ffffff;
    letter-spacing: 0.5px;
  }
  .contact {
    position: absolute;
    right: 24px;
    top: 0;
    text-align: right;
    color: var(--text-light);
  }
  .person-name {
    position: absolute;
    right: 24px; top: 44px;
    margin: 0;
    font-size: 24px;
    font-weight: 600;
    color: var(--name-blue);
    white-space: nowrap;
  }
  .person-title {
    position: absolute;
    right: 24px; top: 78px;
    margin: 0;
    font-size: 16px;
    color: var(--text-light);
    white-space: nowrap;
  }
  .address {
    position: absolute;
    right: 24px; top: 206px;
    margin: 0;
    font-size: 15.5px;
    line-height: 22px;
    text-align: right;
    color: var(--text-light);
    font-style: normal;
  }
  .contact-list {
    position: absolute;
    right: 24px; top: 260px;
    margin: 0; padding: 0;
    list-style: none;
  }
  .contact-list li {
    display: flex;
    justify-content: flex-end;
    align-items: center;
    gap: 10px;
    height: 22px;
    font-size: 15px;
    color: var(--text-light);
    white-space: nowrap;
  }
  .contact-list li.phone {
    color: var(--name-blue);
    font-weight: 600;
    font-size: 16px;
  }
  .contact-list svg { width: 14px; height: 14px; flex: none; }
</style>
</head>
<body>

<section class="card card--front">
  <div class="front-mark">HARBORLINE AUTO</div>
  <div class="front-web">
    <span class="rule"></span>
    <span>www.harborlineautoxq.net</span>
    <span class="rule"></span>
  </div>
</section>

<section class="card card--back">
  <svg class="back-band" viewBox="0 0 620 374" aria-hidden="true">
    <defs>
      <linearGradient id="bandBlue" x1="0" y1="0" x2="0" y2="1">
        <stop offset="0" stop-color="#1b6797"/>
        <stop offset="1" stop-color="#2a85bd"/>
      </linearGradient>
    </defs>
    <path d="M0 0 H270 Q340 190 244 374 H0 Z" fill="var(--gold)"/>
    <path d="M0 0 H240 Q322 190 244 374 H0 Z" fill="url(#bandBlue)"/>
  </svg>

  <div class="brand-circle"></div>
  <div class="brand-name">HARBORLINE AUTO</div>

  <h1 class="person-name">Daniel Rourke</h1>
  <p class="person-title">Managing Director</p>

  <address class="address">2874 Cresthaven Road,<br>Shelbyville, TN 37162</address>

  <ul class="contact-list">
    <li class="phone">931-555-0148
      <svg viewBox="0 0 16 16"><path fill="var(--gold)" d="M1 5c0-2 3-3 7-3s7 1 7 3v1h-3V5H4v1H1zM4 7h8l2 7H2z"/></svg>
    </li>
    <li class="phone">629-555-0173
      <svg viewBox="0 0 16 16"><path fill="var(--gold)" d="M1 5c0-2 3-3 7-3s7 1 7 3v1h-3V5H4v1H1zM4 7h8l2 7H2z"/></svg>
    </li>
    <li>www.harborlineautoxq.net
      <svg viewBox="0 0 16 16"><circle cx="8" cy="8" r="6.5" fill="none" stroke="var(--gold)" stroke-width="1.5"/><path d="M1.5 8h13M8 1.5c-3 3.5-3 9.5 0 13M8 1.5c3 3.5 3 9.5 0 13" fill="none" stroke="var(--gold)" stroke-width="1.2"/></svg>
    </li>
    <li>harborlineautoxq@mailnest.example
      <svg viewBox="0 0 16 16"><rect x="1" y="3" width="14" height="10" fill="var(--gold)"/><path d="M1 3l7 6 7-6" fill="none" stroke="#2a2b2f" stroke-width="1.2"/></svg>
    </li>
  </ul>
</section>

</body>
</html>
```